Corporate Design für Waldsee Gut
Die Desgins sind wunderschön geworden. Die Kommunikation war stets sehr freundlich und schnell. Wir freuen uns auf die auch weiterhin bestehende und Zukünftige Zusammenarbeit.
Zielgruppe
Verkauf von diversen hoch qualitativen Honigprodukten. Produktion eigener Honig Produkte unter der Marke Waldsee Gut.
Online Shop in der Schweiz
Aufgabenstellung
Das Logo soll aus einer Krone mit Gold-Schwarzen Bienen Streifen sein. Das ganze Design soll Bezug zu Honig und Bienen haben.
Wir sind offen für diverse Ideen. (evtl. auch Bezug zu Schweiz)

```html
<!DOCTYPE html>
<html lang="de">
<head>
<meta charset="utf-8">
<title>Waldsee Gut – Geschäftsausstattung</title>
<link rel="stylesheet" href="https://fonts.googleapis.com/css2?family=Raleway:wght@300;400;500&family=Montserrat:wght@400;700&display=swap">
<style>
  :root {
    --canvas: #ffffff;
    --ink: #1a1a1a;
    --text: #3a3a3a;
    --rule: #c9c9c9;
    --gold: #c9a44c;
    --comb-light: #f6f1e6;
    --comb-deep: #ede3cf;
    --card-dark: #000000;
    --paper: #ffffff;
  }
  html, body {
    margin: 0;
    padding: 0;
    width: 1200px;
    height: 1200px;
    overflow: hidden;
    background: var(--canvas);
  }
  .stage {
    position: relative;
    width: 1200px;
    height: 1200px;
    font-family: "Raleway", sans-serif;
    color: var(--text);
  }

  /* Brand wordmark (plain text) */
  .wordmark {
    position: absolute;
    font-family: "Raleway", sans-serif;
    font-weight: 500;
    letter-spacing: 0.04em;
    white-space: nowrap;
    color: var(--ink);
    line-height: 1;
  }

  .honeycomb {
    position: absolute;
    background: linear-gradient(135deg, var(--comb-deep) 0%, var(--comb-light) 55%, rgba(255,255,255,0) 100%);
    opacity: 0.8;
  }

  /* Letterhead */
  .letterhead {
    position: absolute;
    left: 49px; top: 103px;
    width: 716px; height: 1012px;
    background: var(--paper);
    border: 1px solid var(--rule);
    box-sizing: border-box;
  }
  .letterhead .wordmark { left: 538px; top: 137px; font-size: 27px; }
  .fold-mark {
    position: absolute;
    left: -1px; top: 357px;
    width: 18px; height: 1px;
    background: #555;
  }
  .sender-line {
    position: absolute;
    left: 68px; top: 164px;
    font-size: 7px;
    letter-spacing: 0.02em;
    color: var(--text);
  }
  .recipient {
    position: absolute;
    left: 68px; top: 190px;
    font-size: 11px;
    line-height: 17px;
    font-weight: 300;
  }
  .contact-block {
    position: absolute;
    right: 37px; top: 193px;
    text-align: right;
    font-size: 8px;
    line-height: 13px;
  }
  .contact-block p { margin: 0 0 6px; }
  .subject {
    position: absolute;
    left: 68px; top: 325px;
    font-size: 10.6px;
    font-weight: 300;
  }
  .letter-body {
    position: absolute;
    left: 68px; top: 376px;
    font-size: 10.6px;
    line-height: 17px;
    font-weight: 300;
    white-space: nowrap;
  }
  .letter-body p { margin: 0 0 17px; }
  .signature {
    position: absolute;
    left: 68px; top: 738px;
    width: 120px; height: 25px;
    background: linear-gradient(90deg, #2a2a2a 0%, #5a5a5a 100%);
    opacity: 0.15;
    border-radius: 3px;
  }
  .letterhead .honeycomb { left: 0; top: 764px; width: 230px; height: 241px; }
  .bank-details {
    position: absolute;
    right: 37px; top: 947px;
    text-align: right;
    font-size: 8px;
    line-height: 13px;
  }

  /* Business cards */
  .card {
    position: absolute;
    width: 366px; height: 237px;
    box-sizing: border-box;
    overflow: hidden;
  }
  .card-front {
    left: 792px; top: 177px;
    background: var(--card-dark);
  }
  .card-front .wordmark { left: 77px; top: 100px; font-size: 34px; color: var(--gold); }
  .card-back {
    left: 720px; top: 438px;
    background: var(--paper);
    border: 1px solid var(--rule);
  }
  .card-back .wordmark { left: 54px; top: 45px; font-size: 23px; }
  .card-back .honeycomb { left: 0; top: 89px; width: 136px; height: 142px; }
  .card-details {
    position: absolute;
    right: 40px; top: 62px;
    text-align: right;
    font-family: "Montserrat", sans-serif;
    font-size: 10px;
    line-height: 15px;
    letter-spacing: 0.04em;
    color: var(--ink);
  }
  .card-details p { margin: 0 0 6px; }
  .card-details .name { font-weight: 700; }
  .card-details .role { margin-bottom: 26px; }

  /* Jar label */
  .jar-label {
    position: absolute;
    left: 884px; top: 849px;
    width: 182px; height: 189px;
    background: var(--paper);
    border: 1px solid #e6e6e6;
    box-sizing: border-box;
    overflow: hidden;
  }
  .jar-label .wordmark { left: 28px; top: 42px; font-size: 17px; }
  .jar-label .honeycomb { left: 0; top: 89px; width: 87px; height: 93px; }
</style>
</head>
<body>
<div class="stage">

  <section class="letterhead">
    <div class="wordmark">Waldsee Gut</div>
    <div class="sender-line">Musterfirma &nbsp;|&nbsp; Musterstrasse 123 &nbsp;|&nbsp; 12345 Musterstadt</div>
    <div class="recipient">
      Mara Musterfrau<br>Musterfirma<br>Musterstrasse 123<br>12345 Musterstadt
    </div>
    <div class="contact-block">
      <p>Musterstrasse 123<br>12345 Musterstadt</p>
      <p>000.123 456 789<br>000.123 456 790</p>
      <p>info@musterfirma.de<br>www.musterfirma.de</p>
    </div>
    <div class="fold-mark"></div>
    <div class="subject">Ich bin ein Blindtext</div>
    <div class="letter-body">
      <p>Sehr geehrte Frau Musterfrau,</p>
      <p>Weit hinten, hinter den Wortbergen, fern der Länder Vokalien und Konsonantien leben die Blindtexte.<br>
      Abgeschieden wohnen Sie in Buchstabhausen an der Küste des Semantik, eines großen Sprachozeans.<br>
      Ein kleines Bächlein namens Duden fließt durch ihren Ort und versorgt sie mit den nötigen Regelialien.</p>
      <p>Es ist ein paradiesmatisches Land, in dem einem gebratene Satzteile in den Mund fliegen. Nicht einmal<br>
      von der allmächtigen Interpunktion werden die Blindtexte beherrscht – ein geradezu unorthographisches<br>
      Leben. Eines Tages aber beschloß eine kleine Zeile Blindtext, ihr Name war Lorem Ipsum, hinaus zu<br>
      gehen in die weite Grammatik. Der große Oxmox riet ihr davon ab, da es dort wimmele von bösen Kommata,<br>
      wilden Fragezeichen und hinterhältigen Semikoli, doch das Blindtextchen ließ sich nicht beirren.</p>
      <p>Es packte seine sieben Versalien, schob sich sein Initial in den Gürtel und machte sich auf den Weg. Als es<br>
      die ersten Hügel des Kursivgebirges erklommen hatte, warf es einen letzten Blick zurück auf die Skyline<br>
      seiner Heimatstadt Buchstabhausen, die Headline von Alphabetdorf und die Subline seiner eigenen Straße,<br>
      der Zeilengasse. Wehmütig lief ihm eine rethorische Frage über die Wange, dann setzte es seinen Weg<br>
      fort. Unterwegs traf es eine Copy. Die Copy warnte das Blindtextchen, da, wo sie<br>
      herkäme wäre sie...</p>
      <p>Mit freundlichen Grüßen</p>
    </div>
    <div class="signature" role="img" aria-label="Handschriftliche Unterschrift"></div>
    <div class="honeycomb" role="img" aria-label="Zarte goldene Wabenform als Dekor"></div>
    <div class="bank-details">
      Musterbank<br>IBAN DE00 0000 0000 0000 0000 00<br>BIC MUS0000000
    </div>
  </section>

  <section class="card card-front">
    <div class="wordmark">Waldsee Gut</div>
  </section>

  <section class="card card-back">
    <div class="honeycomb" role="img" aria-label="Zarte goldene Wabenform als Dekor"></div>
    <div class="wordmark">Waldsee Gut</div>
    <div class="card-details">
      <p class="name">Max Mustermann</p>
      <p class="role">Geschäftsführung</p>
      <p>Musterstrasse 123<br>12345 Musterstadt</p>
      <p>000.123 456 789<br>000.123 456 790</p>
      <p>info@musterfirma.de<br>www.musterfirma.de</p>
    </div>
  </section>

  <section class="jar-label">
    <div class="honeycomb" role="img" aria-label="Zarte goldene Wabenform als Dekor"></div>
    <div class="wordmark">Waldsee Gut</div>
  </section>

</div>
</body>
</html>
```